Home Remodeling company needs a business card design

we need a business card design for home remodeling company in hamilton county, indiana USA. we offers a wide range of construction services including whole house renovations, Design and Build Basements and Kitchen and Bathroom Remodeling . we would like to see designs for both site of business card that use the same color of the company logo and also including all information below :
1- Karim Feltous CEO / General Contractor
2- all company contacts Telephone numbers ( 1-888-DULOM-47 ) ( 317-555-0193) email address ( info@dulomhome.com) website ( www.dulomhome.com ) and social media logos (Facebook- twitter- google plus )
3- company logo
4- licensed . insured . bonded

```html
<!DOCTYPE html>
<html lang="en">
<head>
<meta charset="utf-8">
<title>Dulom – Business Card</title>
<link href="https://fonts.googleapis.com/css2?family=Roboto:wght@400;700&display=swap" rel="stylesheet">
<style>
  :root {
    --bg: #e6e4e2;
    --card-black: #141414;
    --card-dark: #1c1c1d;
    --red: #e0191f;
    --white: #ffffff;
    --light-grey: #e4e4e4;
    --muted: #444444;
    --text-soft: #d8d8d8;
  }
  * { margin: 0; padding: 0; box-sizing: border-box; }
  html, body { width: 1200px; height: 716px; overflow: hidden; }
  body {
    background: var(--bg);
    font-family: "Roboto", sans-serif;
    position: relative;
  }
  .card {
    position: absolute;
    top: 210px;
    width: 520px;
    height: 297px;
    overflow: hidden;
    box-shadow: 0 10px 28px rgba(0,0,0,.25);
  }
  .card--front { left: 50px; background: var(--card-black); }
  .card--back { left: 630px; background: var(--card-dark); }

  .brand { position: absolute; display: flex; align-items: center; gap: 12px; }
  .brand__square { display: block; background: var(--red); }
  .brand__name { font-weight: 700; line-height: 1; letter-spacing: 2px; color: var(--white); }

  .card--front .brand { left: 50%; top: 50%; transform: translate(-50%, -50%); }
  .card--front .brand__square { width: 16px; height: 16px; background: var(--muted); }
  .card--front .brand__name { font-size: 60px; color: var(--muted); }

  .card--back .brand { right: 40px; top: 78px; }
  .card--back .brand__square { width: 12px; height: 12px; }
  .card--back .brand__name { font-size: 44px; }

  .social { position: absolute; left: 28px; top: 30px; display: flex; gap: 4px; }
  .social__box { width: 14px; height: 14px; background: var(--light-grey); border-radius: 2px; }

  .person { position: absolute; left: 28px; top: 118px; }
  .person__name { color: var(--red); font-weight: 700; font-size: 19px; letter-spacing: .5px; }
  .person__title { color: var(--text-soft); font-size: 12px; margin-top: 4px; }

  .contacts { position: absolute; left: 286px; top: 164px; list-style: none; }
  .contacts__item {
    display: flex; align-items: center; gap: 10px;
    color: var(--white); font-size: 13.5px; line-height: 18px;
  }
  .contacts__icon { width: 10px; height: 10px; fill: var(--red); flex: none; }

  .footer { position: absolute; left: 0; bottom: 0; width: 520px; height: 64px; }
  .footer__text {
    position: absolute; right: 22px; bottom: 13px;
    color: var(--white); font-size: 15px; letter-spacing: .5px;
  }
</style>
</head>
<body>
  <section class="card card--front">
    <div class="brand">
      <span class="brand__square"></span>
      <span class="brand__name">DULOM</span>
    </div>
  </section>

  <section class="card card--back">
    <div class="social" aria-label="Social media">
      <span class="social__box"></span>
      <span class="social__box"></span>
      <span class="social__box"></span>
    </div>

    <div class="brand">
      <span class="brand__square"></span>
      <span class="brand__name">DULOM</span>
    </div>

    <div class="person">
      <p class="person__name">Karim Feltous</p>
      <p class="person__title">CEO / General Contractor</p>
    </div>

    <ul class="contacts">
      <li class="contacts__item">
        <svg class="contacts__icon" viewBox="0 0 10 10"><path d="M2 0.5 L3.6 2.6 L2.7 3.6 Q3.6 5.6 6.3 7.3 L7.4 6.4 L9.5 8 L8.3 9.5 Q2.5 8.5 0.5 1.7 Z"/></svg>
        1-888-DULOM-47
      </li>
      <li class="contacts__item">
        <svg class="contacts__icon" viewBox="0 0 10 10"><rect x="0.5" y="3.5" width="9" height="6" rx="1"/><rect x="2.5" y="0.5" width="5" height="3"/></svg>
        317-555-0193
      </li>
      <li class="contacts__item">
        <svg class="contacts__icon" viewBox="0 0 10 10"><path d="M0.5 2 H9.5 V8.5 H0.5 Z M0.5 2 L5 5.5 L9.5 2" stroke="#1c1c1d" stroke-width="0.8"/></svg>
        info@dulomhome.com
      </li>
      <li class="contacts__item">
        <svg class="contacts__icon" viewBox="0 0 10 10"><circle cx="5" cy="5" r="4.5"/><path d="M0.5 5 H9.5 M5 0.5 Q2.5 5 5 9.5 M5 0.5 Q7.5 5 5 9.5" stroke="#1c1c1d" stroke-width="0.7" fill="none"/></svg>
        www.dulomhome.com
      </li>
    </ul>

    <svg class="footer" viewBox="0 0 520 64" preserveAspectRatio="none" aria-hidden="true">
      <polygon points="0,34 230,34 230,64 0,64" fill="var(--light-grey)"/>
      <polygon points="215,64 245,14 520,14 520,64" fill="var(--red)"/>
    </svg>
    <p class="footer__text">Licensed &nbsp;•&nbsp; Insured &nbsp;•&nbsp; Bonded</p>
  </section>
</body>
</html>
```